business card for a massage therapy practice named 'Cedar and Willow Massage Studio'

I really need a trendy, yet easy on the eyes business card to complement my logo. Ideally with some gold or rose gold foil work.

My uploaded file of the logo I have in horizontal but I have a vertical version as well. Another color that is used in the website is a blush pink here and there. I'd like to see some trendy tropical leaves in the design.

```html
<!DOCTYPE html>
<html lang="en">
<head>
<meta charset="utf-8">
<title>Cedar and Willow Massage Studio — Business Card</title>
<link href="https://fonts.googleapis.com/css2?family=Montserrat:wght@400;500;600;700&display=swap" rel="stylesheet">
<style>
  :root {
    --page: #ecebe7;
    --teal: #6dbba3;
    --teal-deep: #5eaa92;
    --paper: #f7f7f5;
    --gold: #9b7b4b;
    --gold-label: #b0703a;
    --ink: #1e1e1e;
    --white: #ffffff;
  }
  * { box-sizing: border-box; margin: 0; padding: 0; }
  html, body {
    width: 1200px; height: 1200px; overflow: hidden;
    background: var(--page);
    font-family: "Montserrat", sans-serif;
  }
  .sheet {
    position: relative; width: 1200px; height: 1200px;
    display: flex; flex-direction: column; align-items: center; justify-content: center; gap: 60px;
  }
  .card {
    position: relative; width: 840px; height: 480px;
    background: var(--teal); overflow: hidden;
    box-shadow: 0 6px 18px rgba(0,0,0,0.12);
  }

  /* Front */
  .brand {
    position: absolute; left: 0; right: 0; top: 150px;
    display: flex; align-items: center; justify-content: center; gap: 28px;
  }
  .brand-mark {
    width: 74px; height: 74px; border-radius: 50%;
    background: var(--gold); flex: none;
  }
  .brand-name {
    color: var(--ink); font-weight: 500; letter-spacing: 0.04em;
    line-height: 1.15;
  }
  .brand-name .line-main { display: block; font-size: 50px; }
  .brand-name .line-sub { display: block; font-size: 24px; letter-spacing: 0.32em; text-transform: uppercase; }
  .front-web {
    position: absolute; left: 0; right: 0; bottom: 70px;
    text-align: center; color: var(--white);
    font-size: 20px; font-weight: 600; letter-spacing: 0.06em;
  }

  /* Back */
  .swoop { position: absolute; inset: 0; }
  .contact { position: absolute; left: 64px; top: 70px; color: var(--white); }
  .contact-name {
    font-size: 46px; font-weight: 700; letter-spacing: 0.04em; text-transform: uppercase; line-height: 1;
  }
  .contact-role { font-size: 24px; font-weight: 600; margin-top: 8px; }
  .contact-address { font-size: 22px; font-weight: 400; line-height: 1.35; margin-top: 52px; letter-spacing: 0.02em; }
  .contact-lines { list-style: none; font-size: 22px; line-height: 1.35; margin-top: 34px; letter-spacing: 0.02em; }
  .contact-lines .label { color: var(--gold-label); font-weight: 700; }
  .back-mark {
    position: absolute; right: 44px; top: 44px;
    width: 40px; height: 40px; border-radius: 50%; background: var(--gold);
  }
</style>
</head>
<body>
<main class="sheet">

  <section class="card card-front" aria-label="Card front">
    <div class="brand">
      <span class="brand-mark" aria-hidden="true"></span>
      <div class="brand-name">
        <span class="line-main">Cedar and Willow</span>
        <span class="line-sub">Massage Studio</span>
      </div>
    </div>
    <p class="front-web">www.cedarandwillow.com</p>
  </section>

  <section class="card card-back" aria-label="Card back">
    <svg class="swoop" viewBox="0 0 840 480" aria-hidden="true">
      <path d="M700 0 C 690 120, 760 220, 840 300 L 840 0 Z" fill="var(--paper)"/>
      <path d="M676 0 C 668 130, 740 240, 840 330" fill="none" stroke="var(--gold)" stroke-width="7"/>
      <path d="M660 0 C 650 140, 726 256, 840 352" fill="none" stroke="var(--gold)" stroke-width="4"/>
    </svg>
    <span class="back-mark" aria-hidden="true"></span>
    <div class="contact">
      <h1 class="contact-name">Dana Whitlow</h1>
      <p class="contact-role">Design Consultant</p>
      <p class="contact-address">482 Linden Row NE, Atlanta,<br>Georgia, GA 30310</p>
      <ul class="contact-lines">
        <li><span class="label">Phone:</span> 310.555.0142</li>
        <li><span class="label">Email:</span> hello@SoftHarbor.com</li>
        <li><span class="label">Web:</span> www.SoftHarbor.com</li>
      </ul>
    </div>
  </section>

</main>
</body>
</html>
```